Letter design, envelope design, and more

Hello, we the Tavrin Gmbh are looking for our shop. Letter C5. Design does not have to be like a business card, so it can have straight lines. Only the color is important. The logo is the text under TaVRin omit.It should not be playful but Profesionel

Font styles to use
Sans Serif

Colors
0555a3
3176b5
85abd2
85cae6
34a7d8
0792cd
cee9f5
cfdfed
000000

Requirements
Must have
• Color like business card, Please, with the text under TaVRin, Correct address Lindmattstr. 4 Zip code 9517 Seewil, as well as Couvert Without addressing only design and logo with TaVrn
Nice to have
• more writing articles
Should not have
• Not too colored, Text under TaVRin, bright colors

```html
<!DOCTYPE html>
<html lang="de">
<head>
<meta charset="utf-8">
<title>Tavrin Gmbh – Briefschaften</title>
<link href="https://fonts.googleapis.com/css2?family=Source+Sans+3:wght@400;600;700&display=swap" rel="stylesheet">
<style>
:root{
  --navy:#031c6e;
  --sky:#a9c5d8;
  --slate:#8aa0b8;
  --paper:#ffffff;
  --ink:#111111;
  --stage:#e6e9ea;
}
*{margin:0;padding:0;box-sizing:border-box}
html,body{width:1200px;height:1123px;overflow:hidden}
body{background:var(--stage);font-family:"Source Sans 3",Arial,sans-serif;color:var(--ink);position:relative}
.sheet{position:absolute;background:var(--paper);box-shadow:0 2px 6px rgba(0,0,0,.12);overflow:hidden}
.band{position:absolute;left:0;top:0;width:100%;background:var(--navy)}
.flap{position:absolute;left:0;top:0;width:100%}
.flap-name{position:absolute;left:0;width:100%;text-align:center;color:#fff;font-weight:700;letter-spacing:.5px}
.brand{position:absolute;display:flex;align-items:center;gap:6px;color:var(--navy);font-weight:700;letter-spacing:.3px}
.brand-square{background:var(--navy)}
.web-tag{position:absolute;right:0;bottom:16px;background:var(--sky);color:#fff;display:flex;align-items:center;justify-content:center;letter-spacing:1.6px;font-size:6px}
.env-tall{left:67px;top:195px;width:290px;height:413px}
.letterhead-blank{left:388px;top:198px;width:292px;height:411px}
.letter{left:730px;top:109px;width:400px;height:567px}
.letter .band{height:19px}
.letter-body{position:absolute;left:59px;top:155px;width:282px;font-size:7.6px;line-height:8.7px}
.letter-body p{margin-bottom:8.6px}
.salutation{margin-bottom:27px !important}
.signature{width:60px;height:34px;margin-top:32px;background:linear-gradient(90deg,#f2f2f2,#e6e6e6)}
.signer{margin-top:4px;font-size:7.8px;line-height:12px}
.footer-block{position:absolute;left:0;top:512px;width:103px;height:43px;background:var(--sky)}
.contacts{position:absolute;left:119px;top:519px;display:flex;gap:14px;font-size:5.6px;font-weight:600}
.contact{display:flex;flex-direction:column;align-items:center;gap:3px}
.contact svg{width:16px;height:16px}
.divider{border-left:1px solid #555;padding-left:3px;margin-left:3px}
.env-wide{left:164px;top:732px;width:412px;height:290px}
.letterhead-wide{left:607px;top:732px;width:410px;height:290px}
</style>
</head>
<body>

<section class="sheet env-tall" aria-label="Couvert Hochformat">
  <svg class="flap" viewBox="0 0 290 62" height="62" aria-hidden="true">
    <path d="M0 0H290L276 45Q271 60 254 60H36Q19 60 14 45Z" fill="var(--navy)"/>
  </svg>
  <div class="flap-name" style="top:20px;font-size:17px">TaVrn</div>
</section>

<section class="sheet letterhead-blank" aria-label="Briefbogen leer">
  <div class="band" style="height:18px"></div>
  <div class="brand" style="left:24px;top:33px;font-size:15px">
    <span class="brand-square" style="width:14px;height:14px"></span>TaVRin
  </div>
  <div class="web-tag" style="width:98px;height:40px">www.tavrin.ch</div>
</section>

<section class="sheet letter" aria-label="Brief">
  <div class="band"></div>
  <div class="brand" style="left:24px;top:40px;font-size:21px">
    <span class="brand-square" style="width:20px;height:20px"></span>TaVRin
  </div>
  <div class="letter-body">
    <p class="salutation">Dear Mr. Keller,</p>
    <p>Lorem ipsum dolor sit amet, consectetur adipiscing elit. Cras elementum eget sem quis tincidunt. Suspendisse congue accumsan ipsum ac auctor.</p>
    <p>Fusce sagittis tellus a urna ornare eleifend. Interdum et malesuada fames ac ante ipsum primis in faucibu. Fusce pulvinar sodales diam et consequat. Praesent placerat nulla vitae nisl ullamcorper, vel facilisis lorem consequat. Fusce sagittis tellus a urna ornare eleifend. Interdum et malesuada fames ac ante ipsum primis in faucibu. Fusce pulvinar sodales diam et consequat. Praesent placerat nulla vitae nisl ullamcorper, vel facilisis lorem consequat.</p>
    <p>Fusce sagittis tellus a urna ornare eleifend. Interdum et malesuada fames ac ante ipsum primis in faucibu. Fusce pulvinar sodales diam et consequat. Praesent placerat nulla vitae nisl ullamcorper, vel facilisis lorem consequat.</p>
    <p>Lorem ipsum dolor sit amet, consectetur adipiscing elit. Cras elementum eget sem quis tincidunt.</p>
    <div class="signature" role="img" aria-label="Handschriftliche Unterschrift"></div>
    <p class="signer">Lukas Berger<br>Co Founder &amp; CEO</p>
  </div>
  <div class="footer-block"></div>
  <div class="contacts">
    <div class="contact">
      <svg viewBox="0 0 16 16" aria-hidden="true"><circle cx="8" cy="8" r="7" fill="none" stroke="#222"/><circle cx="8" cy="8" r="4" fill="none" stroke="#222" stroke-width=".8"/><path d="M4 8H12M8 4V12" stroke="#222" stroke-width=".8"/></svg>
      <span>www.tavrin.ch</span>
    </div>
    <div class="contact">
      <svg viewBox="0 0 16 16" aria-hidden="true"><circle cx="8" cy="8" r="7" fill="none" stroke="#222"/><path d="M5.5 4.5L7 6.5 6 7.5Q7 9.5 8.5 10L9.5 9 11.5 10.5 10.5 11.8Q7 11.5 4.5 6Z" fill="#222"/></svg>
      <span>+41 71 555 02 40</span>
    </div>
    <div class="contact">
      <svg viewBox="0 0 16 16" aria-hidden="true"><circle cx="8" cy="8" r="7" fill="none" stroke="#222"/><path d="M4.5 8L11.5 5 9.5 11.5 8 9Z" fill="none" stroke="#222" stroke-width=".8"/></svg>
      <span>info@tavrin.ch</span>
    </div>
    <div class="contact">
      <svg viewBox="0 0 16 16" aria-hidden="true"><circle cx="8" cy="8" r="7" fill="none" stroke="#222"/><path d="M8 12.5Q5 9 5 7A3 3 0 0 1 11 7Q11 9 8 12.5Z" fill="none" stroke="#222" stroke-width=".8"/><circle cx="8" cy="7" r="1" fill="#222"/></svg>
      <span>Lindmattstr. 4 <span class="divider">9517 Seewil</span></span>
    </div>
  </div>
</section>

<section class="sheet env-wide" aria-label="Couvert C5">
  <svg class="flap" viewBox="0 0 412 60" height="60" aria-hidden="true">
    <path d="M0 0H412L394 44Q387 59 366 59H46Q25 59 18 44Z" fill="var(--navy)"/>
  </svg>
  <div class="flap-name" style="top:18px;font-size:18px">TaVrn</div>
</section>

<section class="sheet letterhead-wide" aria-label="Briefbogen quer">
  <div class="band" style="height:18px"></div>
  <div class="brand" style="left:28px;top:42px;font-size:18px">
    <span class="brand-square" style="width:17px;height:17px"></span>TaVRin
  </div>
  <div class="web-tag" style="width:98px;height:40px">www.tavrin.ch</div>
</section>

</body>
</html>
```